Brochure Brightwell Hearth Partners

Brochure 12 x 9 tri fold with insert/ Rack card 9x4. Brightwell Hearth Partners 318 Corvane Street Easton, MD 21629410-822-2207AgingAtHomeSolution.com Tag: Devoted to Thoughtful Household Support.
What we do: Home care agency that services higher end Clients Artsy area on the water. Taking care of seniors in their home.

Our story: Opening Brightwell Hearth Partners, Inc. is my way of making a difference in an industry that is dominated by franchises that often have their policies dictated by corporate policy-makers who are unfamiliar with local customs. My goal is to raise the level of non-medical home health care in our area by providing additional, customized training, higher wages for our care-partners and an inclusive workforce in the decision-making process when developing customized care planning for our clients. Through collaboration with the client, their family and care-partners I have learned what issues, concerns and disappointments may arise which enables me to provide a more defined solution for those in need.My goal of providing superior training required locating a nationally recognized curriculum that would serve our clients’ needs. I found the perfect fit with Norla Vance’s, Kindred Pathway Method™ and her Shifting Stones Series™. These programs provide our care-partners with the tools needed to handle the challenges of natural aging and living with Dementia. I was so impressed with these programs, I became a Certified Independent Trainer; one of five in the State of Lindhaven. There is a bonus for our care-partners who are required to maintain Continuing Education Units - these programs qualify for credit! Improving our industry by providing exemplary care-partners is my goal!I look forward to assisting you with your needs! Dana Prewitt Owner

Services: Companion Care Service - Conversation and Companionship , Meal Preparation, Light House Keeping, Errand Service ,Grocery Shopping ,Incidental Transportation, Laundry & Linen Washing, Medication Reminders, Recreational Activities ,
Personal Care Services: Bathing ,Mobility ,Transferring & Positioning ,Incontinence Care ,Oral Hygiene ,Feeding, Toileting ,Grooming & Dressing, Special Diet Preparation.

Our Commitment to You: Extensive Care-Partner Education - We provide, in addition to state mandated training, eight additional hours of hands-on Dementia training from a Certified, Independent Instructor on the “Kindred Pathway Method” by Norla Vance, a nationally recognized instructor on aging.

Nutrition/Local Chef Inspired Training ;We provide six, two-hour food preparation sessions for our care-partners using local chefs, their recipes and locally grown food.

Meaningful & Engaging Activities - We provide a monthly list with local activities to our care-partners based on our client’s interest and capabilities. Focusing on what our client loved to do in the past.

Home Solutions When Needed; We provide management services to help keep our clients in their homes by working with current contractors or locating new ones to properly maintain a safe-living environment.

About owner: Dana Prewitt, owner of Brightwell Hearth Partners, has earned her certification as an Independent Trainer in the Kindred Pathway; Method (KPM) by Norla Vance, a nationally recognized instructor on natural aging and aging with Dementia. Dana is one of five certified independent trainers in the state of Lindhaven. All staff will have eight hours of hands on Dementia Kindred Pathway Method training.

On the insert 11x 4.25 want the top to be sticking out of the tri -fold "Dementia Experts . I would like to have shades of each STONE as it progresses
The Shifting STONES(R): The STONES model recognizes the dynamic nature of the human brain and its abilities. Unlike other cognitive models, it acknowledges that everyone’s abilities can change in a moment. Modifying environments, situations, interactions, and expectations will create either supportive positive opportunities or result in distress and a sense of failure. Just as gemstones need different settings and care to show their best characteristics, so do people. Rather than focusing on a person’s loss when there is brain change, seeing individuals as precious, unique, and capable encourages a care partnership and is the core of this model. Providing supportive settings for everyone, including care providers, allows them to use what they have to be their best. The STONES® advocate that everyone living with brain change when given the opportunity will shine. Norla Vance and Kindred Pathway Method

Sapphire ~ True Blue ~ Optimal Cognition, Healthy Brain•
True to self: personal preferences remain basically the same
• Can be flexible in thinking and appreciate multiple perspectives
• Stress/pain/fatigue may trigger Diamond state: back to Sapphire with relief
• Able to suppress and filter personal reactions: chooses effective responses
• Selects from options and can make informed decisions
• Processes well and able to successfully transition
• Aging doesn’t change ability: processing slows, more effort/time/practice needed
My brain is healthy - true blue. If I am aging normally or distressed, it may be hard for me to find words. I can describe what I am thinking so you understand. I may talk to myself because I am giving myself cues and prompts. I can learn new things and change habits, but it takes time and effort. Honoring my choices and preferences, when possible, is important. I need more time to make decisions. Give me the details and let me think about it before you need an answer. I am able to remember plans and information but supports are helpful. I may like specific prompts such as notes, calendars, and reminder calls. Health changes in vision, hearing, balance, coordination, depression, anxiety, pain, or medication may impact my behavior, but my cognitive abilities remain the same.

Diamond ~ Clear and Sharp ~ Routines and Rituals Rule
• Displays many facets: behavior and perspective can shift dramatically
• Prefers the familiar and may resist change: challenged by transitions
• More rigid and self-focused; sees wants as needs, when stressed
• Personal likes/dislikes in relationships/space/belongings etc, become more intense
• Reacts to changes in environment; benefits from familiar; functional/forgiving
• Needs repetition and time to absorb new/different information or routines
• Trusted authority figures can help: reacts better when respect is mutual
My overall cognition is clear and sharp. When happy and supported, I am capable and shine in my abilities. When distressed, I can be cutting and rigid and may see help as a threat. I have trouble seeing other points of view and may become less aware of boundaries or more possessive about my relationships, personal space, and belongings. I have many facets so people see me differently depending on the situation. This can cause conflict among my family, friends, or care team as it’s hard to tell if I am choosing my behavior or truly have limits in my ability. I can socially engage and have good cover skills. People will vary in their awareness of what is happening to me. I want to keep habits and environments as they have always been, even if they are problematic for me or others. I am often focused on the past, personal values, or finances. I will need help to make changes in my life; it’s hard for me. I can be in a Diamond state for reasons other than dementia.

Emerald ~ Green and On the Go With a Purpose ~ Naturally Flawed
• Sees self as able and independent, with limited awareness of changes in ability
• Lives in moments of clarity mixed with periods of loss in logic/reason/perspective
• Understanding and use of language change: vague words and many repeats
• Cues and support help when getting to/from places and doing daily routines
• Awareness of time, place, and situation will not always match current reality
• Strong emotional reactions are triggered by fears, desires, or unmet needs
Needs to know what comes next: seeks guidance and assistance to fill the day
I am flawed; it is part of being a natural emerald. I tend to be focused on what I want or need in this moment and may not be aware of my own safety or changing abilities. I can chat socially, but I typically miss one out of every four words and cannot accurately follow the meaning of longer conversations. I won’t remember the details of our time together, but I will remember how your body language and tone of voice made me feel. I may hide or misplace things and believe someone has taken them. My brain will make up information to fill in the blanks, which makes you think I am lying. If you try to correct me or argue, I may become resentful or suspicious of you. I am not always rational, but I don’t want to be made to feel incompetent. My brain plays tricks on me, taking me to different times and places in my life. When I am struggling, I may tell you, “I want to go home.” To provide the help and assistance I need, you must go with my flow, use a positive, partnered approach, and modify my environment.

Amber ~ Caught in a Moment of Time ~ Caution Required
• Focused on sensation: seeks to satisfy desires and tries to avoid what is disliked
•Environment can drive actions and reactions without awareness of safety
• Visual abilities are limited: focus is on pieces or parts, not the whole picture
• What happens to or around an Amber, may cause strong and surprising reactions
• Enters others’ space and crosses boundaries attempting to meet own needs
• Has periods of intense activity: may be very curious or repetitive with objects or actions
• Care is refused or seen as threatening, due to differences in perspective and ability.
Like a particle trapped in an amber, I am caught in a moment of time. It may surprise you to see how I take in the world around me. I may not know you or see you as a whole person. I react to you based on how you look, sound, move, smell, and respond to me. I like to do simple tasks over and over and may need to repeatedly move and touch, smell, taste, take or tear items apart. While it may exhaust or frustrate you, it soothes me. I don’t recognize danger; you will have to safeguard my environment. I’m intolerant to discomfort because my mouth, hands, feet, and genitalia are highly sensitive due to changes in my nervous system. Therefore, activities like eating, taking medication, mouth care, bathing, dressing, and toileting may distress me. Please notice my reaction and stop if I am resisting. I can’t help myself and one or both of us may get hurt emotionally and/or physically. If this happens, wait a few minutes, connect with me, and try a different approach; possibly substituting one area of focus for another.

Ruby ~ Deep and Strong in Color ~ Others Stop Seeing What is Possible
• Makes use of rhythm: can usually sing, hum, pray, sway, rock, clap, and dance
• When moving can’t stop; when stopped can’t get moving: needs guidance and help
• Big, strong movements are possible, while skilled abilities are being lost
• Danger exists due to limited abilities combined with automatic actions or reactions
• Tends to miss subtle hints, but gets magnified facial expressions and voice rhythms
• Can mimic actions or motions, but will struggle to understand instructions/gestures
• Able to pick up and hold objects, and yet not know what to do with them
As the deep red of a ruby masks detail, my obvious losses make my remaining abilities harder to notice. Although my fine motor skills have become very limited, remember that I am able to move and do simple things with my hands. You will need to anticipate, identify, and respond to all of my needs, even though I may not be aware of them. Plan to create a supportive environment, help with the details of care, and structure my day. Just as a crossing guard directs traffic, you will need to guide my movements and transitions. I can rarely stop or start on my own and switching gears is a challenge. Move with me first, then use your body to show me what you want me to do next, going one step at a time. Palm-beneath-Palm™ assistance helps me to feel safe and secure and to know what to do. Danger is part of my life, due to losses in visual skills, chewing abilities, balance, and coordination. You can reduce the risks to me, but not eliminate them. I can still have moments of joy when you are able to provide what gives me pleasure.

Pearl ~ Hidden Within a Shell ~ Beautiful Moments to Behold
• Will frequently recognize familiar touches, voices, faces, aromas, and tastes• Personhood survives, although all other capabilities are minimal
• Understanding input takes time: go slow and simplify for success
• In care, first get connected by offering comfort then use careful and caring touch
• Changes in the body are profound: weight loss, immobility, systems are failing
• As protective reflexes are lost, breathing, swallowing, and moving will be difficult
Care partners benefit from learning the art of letting go rather than simply giving up
While hidden like a pearl in an oyster shell, I will still have moments when I become alert and responsive. I am near the end of my life. Moments of connection create a sense of wholeness and value between us. Use our time together not just to provide care, but to comfort and connect with me. To help me complete life well, it’s important to honor my personhood when making medical or care decisions; please don’t talk about me as though I am not still here. I respond best to familiar voices and gentle rhythmic movements. I am ruled by reflexes and will startle easily. My brain is losing its ability to control and heal my body. Be prepared to see me having difficulty breathing or swallowing. My body may no longer desire food and drink as I prepare to leave this life. I may not be able to stop living without permission from you. Your greatest gift at this time in my life is to let me know that it is okay to go.

Target Market(s)

Children of seniors, seniors , rehabilitation centers

Requirements
Must have
• Nice photos of Seniors that are happy doing thing they like to do with help (Caregivers)
• Upbeat . Positive
Nice to have
• Processional looking - but very personal, we are taking care of their love ones
Should not have
• Not to feel like a cold hospital or end of life

```html
<!DOCTYPE html>
<html lang="en">
<head>
<meta charset="utf-8">
<title>Brightwell Hearth Partners – Brochure, Rack Card and Insert</title>
<link rel="stylesheet" href="https://fonts.googleapis.com/css2?family=Open+Sans:wght@300;400;600&family=Playfair+Display:wght@400;700&display=swap">
<style>
:root{
  --board:#bcbdc0;
  --navy:#2b2a78;
  --navy-deep:#262469;
  --blue:#1a78b4;
  --sky:#2f8fc8;
  --ink:#232323;
  --white:#ffffff;
  --emerald:#8cc63f;
  --amber:#f0922e;
  --ruby:#e2352e;
  --pearl:#c7a6d0;
  --sapphire:#5b7fd2;
  --diamond:#a7cdea;
}
*{box-sizing:border-box;margin:0;padding:0}
html,body{width:1200px;height:2182px;overflow:hidden}
body{background:var(--board);position:relative;font-family:"Open Sans",Arial,sans-serif;color:var(--ink)}
.piece{position:absolute;overflow:hidden;background:var(--white)}
.panel{position:absolute;top:0;bottom:0;overflow:hidden}
.photo{position:absolute}
.brand-name{font-family:"Playfair Display",Georgia,serif;font-weight:400;color:var(--blue);line-height:1.02}

/* footer bands */
.band{position:absolute;left:0;right:0;bottom:0;height:30px}
.band svg{position:absolute;inset:0;width:100%;height:100%}
.band-text{position:absolute;bottom:9px;font-size:9px;color:var(--white);letter-spacing:.1px;white-space:nowrap}

/* outside trifold */
.outside{left:83px;top:70px;width:722px;height:538px}
.story{left:0;width:241px}
.story h2{position:absolute;left:34px;top:34px;font-family:"Playfair Display",Georgia,serif;font-weight:400;font-size:22px;color:var(--navy)}
.story-body{position:absolute;left:34px;top:75px;width:182px;font-size:8.3px;line-height:10.4px;text-align:justify}
.story-body p{margin-bottom:10px}
.story-sign{margin-top:6px;line-height:10px;text-align:left}
.cover-back{left:241px;width:238px;background:linear-gradient(180deg,#1a7ab2 0%,#26549a 45%,#2b2a78 100%);color:var(--white);text-align:center}
.cover-back .tag{position:absolute;left:0;right:0;top:38px;font-family:"Playfair Display",Georgia,serif;font-size:17px;line-height:21px}
.cover-back .circle-photo{left:28px;top:123px;width:182px;height:182px;border-radius:50%;background:radial-gradient(circle at 40% 45%,#e9ddd0 0%,#c9b7a4 45%,#8f8476 100%)}
.bubble{position:absolute;border-radius:50%;background:rgba(120,170,230,.28)}
.cover-back .brand-name{position:absolute;left:0;right:0;top:328px;color:var(--white);font-size:27px}
.address{position:absolute;left:0;right:0;top:440px;font-family:"Playfair Display",Georgia,serif;font-size:10.5px;line-height:14px}
.cover{left:479px;width:243px}
.cover-top{position:absolute;left:0;right:0;top:0;height:330px;text-align:center}
.cover .brand-name,.rack .brand-name{position:absolute;left:0;right:0;top:30px;font-size:29px}
.welcome{position:absolute;left:0;right:0;font-family:"Playfair Display",Georgia,serif;color:#555;font-size:13px;line-height:17px}
.phone-line{position:absolute;left:0;right:0;font-family:"Playfair Display",Georgia,serif;color:var(--blue);font-size:16px}
.tagline{position:absolute;left:0;right:0;font-family:"Playfair Display",Georgia,serif;color:var(--navy);font-size:16px;line-height:20px}
.cover .hero{left:0;right:0;top:258px;bottom:0;background:linear-gradient(180deg,#f7f3ee 0%,#ead8c8 20%,#cfa98e 55%,#d9cbd8 100%)}

/* inside trifold */
.inside{left:83px;top:629px;width:720px;height:540px}
.services{left:0;width:242px;background:linear-gradient(180deg,#244a92 0%,#2b2a78 100%);color:var(--white)}
.services-head{position:absolute;left:0;right:0;top:0;height:61px;background:linear-gradient(90deg,#2b3a86,#1c6aab)}
.services-head h2{position:absolute;left:25px;top:20px;font-family:"Playfair Display",Georgia,serif;font-weight:400;font-size:22px}
.services .photo{left:0;right:0;top:61px;height:144px;background:linear-gradient(180deg,#7c6a58 0%,#9a7c66 40%,#5c6f48 100%)}
.service-group{position:absolute;left:28px}
.service-group h3{font-family:"Playfair Display",Georgia,serif;font-weight:700;font-size:12.5px;margin-bottom:2px}
.service-group ul{list-style:none}
.service-group li{font-size:9.8px;line-height:13.9px;padding-left:12px;position:relative;color:#dfe7f6}
.service-group li::before{content:"";position:absolute;left:1px;top:5px;width:4px;height:4px;border-radius:50%;background:var(--sky)}
.commitment{left:242px;width:237px}
.commitment h2,.about h2{position:absolute;top:22px;font-family:"Playfair Display",Georgia,serif;font-weight:400;font-size:22px;line-height:25px;color:var(--navy)}
.commitment h2{left:17px}
.pledge{position:absolute;left:17px;width:210px}
.pledge h3{font-family:"Playfair Display",Georgia,serif;font-weight:700;font-size:10.5px;color:var(--blue);margin-bottom:8px}
.pledge p{width:138px;font-size:8.2px;line-height:10.2px}
.pledge .dot{position:absolute;right:0;top:14px;width:71px;height:71px;border-radius:50%}
.about{left:479px;width:241px}
.about h2{left:7px}
.about .photo{left:0;right:0;top:61px;height:144px;background:linear-gradient(160deg,#e7c7ae 0%,#d9a88a 45%,#8aa25a 100%)}
.about-text{position:absolute;left:26px;width:187px;font-size:8.2px;line-height:10.4px;text-align:justify}
.about-sub{position:absolute;left:26px;top:349px;font-family:"Playfair Display",Georgia,serif;font-weight:700;font-size:10.5px;color:var(--blue)}
.about .brand-name{position:absolute;left:25px;top:452px;font-size:17px;white-space:nowrap}
.inside-band{position:absolute;left:242px;right:0;bottom:0;height:32px}
.inside-band svg{position:absolute;inset:0;width:100%;height:100%}

/* rack cards */
.rack{width:244px;height:538px}
.rack-back{left:896px;top:382px;background:linear-gradient(180deg,#fbf8f4 0%,#eadccf 50%,#d8c3c7 100%)}
.rack-front{left:850px;top:339px}
.rack .hero{left:0;right:0;top:258px;bottom:0;background:linear-gradient(180deg,#f7f3ee 0%,#ead8c8 20%,#cfa98e 55%,#d9cbd8 100%)}
.rack-top{position:absolute;left:0;right:0;top:0;height:330px;text-align:center}

/* insert */
.insert{width:367px;height:826px}
.insert-a{left:196px;top:1268px}
.insert-b{left:630px;top:1268px}
.insert-head{position:absolute;left:0;right:0;top:0;height:91px;background:linear-gradient(90deg,#2b2a78 0%,#2b3f8c 55%,#1d78b4 100%)}
.insert-head .brand-name{position:absolute;left:36px;top:30px;color:var(--white);font-size:26px;white-space:nowrap}
.stones-mark{position:absolute;left:22px;top:97px;width:100px;height:100px;border-radius:50%;border:3px solid #d8d4cc;background:radial-gradient(circle,#fbf8f1 0 55%,#efe9dd 56% 100%)}
.training{position:absolute;left:145px;top:112px;color:var(--navy);font-weight:300;font-size:17.5px;line-height:21px}
.training strong{display:block;color:var(--blue);font-weight:600;font-size:31px;line-height:34px}
.insert-a h2{position:absolute;left:22px;top:218px;font-family:"Playfair Display",Georgia,serif;font-weight:400;font-size:17px;color:var(--blue)}
.model-text{position:absolute;left:22px;top:245px;width:323px;font-size:10.2px;line-height:11.6px;text-align:justify}
.model-credit{position:absolute;left:22px;top:409px;font-size:9px;font-weight:600;font-style:italic}
.stone{position:absolute;left:0;right:0;background:linear-gradient(180deg,var(--tone) 0%,#ffffff 88%)}
.stone-icon{position:absolute;left:22px;top:12px;width:47px;height:47px;border-radius:50%}
.stone h3{position:absolute;left:91px;top:8px;font-family:"Playfair Display",Georgia,serif;font-weight:700;font-size:18px;color:var(--white);letter-spacing:.3px}
.stone .sub{position:absolute;left:91px;top:30px;font-size:10px;line-height:12px;color:#333}
.stone ul{position:absolute;left:28px;right:14px;top:68px;list-style:none}
.stone li{position:relative;padding-left:14px;font-size:8.6px;line-height:10.3px}
.stone li::before{content:"";position:absolute;left:1px;top:3px;width:5px;height:5px;border-radius:50%;background:var(--dot)}
.insert-foot{position:absolute;left:0;right:0;bottom:0;height:40px;background:linear-gradient(90deg,#2b2a78,#26549a);color:var(--white);font-size:15px;font-weight:300;line-height:40px;text-align:center;letter-spacing:.3px}
.insert-b .base{position:absolute;left:0;right:0;bottom:0;height:9px;background:var(--navy)}
</style>
</head>
<body>

<section class="piece outside">
  <div class="panel story">
    <h2>Our Story</h2>
    <div class="story-body">
      <p>Opening Brightwell Hearth Partners, Inc. is my way of making a difference in an industry that is dominated by franchises that often have their policies dictated by corporate policy-makers who are unfamiliar with local customs. My goal is to raise the level of non-medical home health care in our area by providing additional, customized training, higher wages for our care-partners and an inclusive workforce in the decision-making process when developing customized care planning for our clients. Through collaboration with the client, their family and care-partners I have learned what issues, concerns and disappointments may arise which enables me to provide a more defined solution for those in need.</p>
      <p>My goal of providing superior training required locating a nationally recognized curriculum that would serve our clients’ needs. I found the perfect fit with Norla Vance’s, Kindred Pathway Method™ and her Shifting Stones Series™. These programs provide our care-partners with the tools needed to handle the challenges of natural aging and living with Dementia. I was so impressed with these programs, I became a Certified Independent Trainer; one of five in the State of Lindhaven. There is a bonus for our care-partners who are required to maintain Continuing Education Units - these programs qualify for credit! Improving our industry by providing exemplary care-partners is my goal!</p>
      <p>I look forward to assisting you with your needs!</p>
      <p class="story-sign">Dana Prewitt<br>Owner</p>
    </div>
    <div class="band">
      <svg viewBox="0 0 241 30" preserveAspectRatio="none"><polygon points="0,20 60,20 60,30 0,30" fill="#2f8fc8"/><polygon points="78,0 241,0 241,30 52,30" fill="#2b2a78"/></svg>
      <span class="band-text" style="left:78px">brightwellhearthpartners.example</span>
    </div>
  </div>

  <div class="panel cover-back">
    <p class="tag">Devoted to Thoughtful<br>Household Support.</p>
    <div class="photo circle-photo" role="img" aria-label="Photo of a smiling senior man sharing a drink with a caregiver"></div>
    <span class="bubble" style="left:184px;top:245px;width:46px;height:46px"></span>
    <span class="bubble" style="left:170px;top:282px;width:22px;height:22px"></span>
    <p class="brand-name">Brightwell<br>Hearth<br>Partners</p>
    <p class="address">Servicing The<br>Harrow Bay Shore of Lindhaven<br>318 Corvane Street<br>Kestrel Point, LH 21775<br>410-555-0148<br>BrightwellHearthPartners.example</p>
  </div>

  <div class="panel cover">
    <div class="photo hero" role="img" aria-label="Photo of a young caregiver hugging a smiling senior woman"></div>
    <div class="cover-top">
      <p class="brand-name">Brightwell<br>Hearth<br>Partners</p>
      <p class="welcome" style="top:148px">Welcome to<br>Brightwell Hearth Partners</p>
      <p class="phone-line" style="top:186px">410-555-0148</p>
      <p class="tagline" style="top:206px">Devoted to Thoughtful<br>Household Support.</p>
    </div>
    <div class="band">
      <svg viewBox="0 0 243 30" preserveAspectRatio="none"><polygon points="0,0 178,0 198,30 0,30" fill="#2b2a78"/><polygon points="186,20 243,20 243,30 192,30" fill="#2f8fc8"/></svg>
      <span class="band-text" style="left:10px">brightwellhearthpartners.example</span>
    </div>
  </div>
</section>

<section class="piece inside">
  <div class="panel services">
    <div class="services-head"><h2>Services</h2></div>
    <div class="photo" role="img" aria-label="Photo of a senior woman with a walker and her caregiver outside a brick home"></div>
    <span class="bubble" style="left:196px;top:300px;width:48px;height:48px"></span>
    <span class="bubble" style="left:178px;top:370px;width:60px;height:60px"></span>
    <span class="bubble" style="left:198px;top:228px;width:14px;height:14px"></span>
    <span class="bubble" style="left:218px;top:455px;width:24px;height:24px"></span>
    <div class="service-group" style="top:226px">
      <h3>Companion Care Service</h3>
      <ul>
        <li>Conversation &amp; Companionship</li><li>Meal Preparation</li><li>Light House Keeping</li><li>Errand Service</li><li>Grocery Shopping</li><li>Incidental Transportation</li><li>Laundry &amp; Linen Washing</li><li>Medication Reminders</li><li>Recreational Activities</li>
      </ul>
    </div>
    <div class="service-group" style="top:382px">
      <h3>Personal Care Services</h3>
      <ul>
        <li>Bathing</li><li>Mobility</li><li>Transferring &amp; Positioning</li><li>Incontinence Care</li><li>Oral Hygiene</li><li>Feeding</li><li>Toileting</li><li>Grooming &amp; Dressing</li><li>Special Diet Preparation</li>
      </ul>
    </div>
  </div>

  <div class="panel commitment">
    <h2>Our Commitment<br>to You</h2>
    <div class="pledge" style="top:88px">
      <h3>Extensive Care-Partner Education</h3>
      <p>We provide, in addition to state mandated training, eight additional hours of hands-on Dementia training from a Certified, Independent Instructor on the “Kindred Pathway Method” by Norla Vance, a nationally recognized instructor on aging.</p>
      <span class="dot" style="top:16px;background:#eef2f7;border:3px solid #2b3a86" role="img" aria-label="Trainer certification badge"></span>
    </div>
    <div class="pledge" style="top:210px">
      <h3>Nutrition/Local Chef Inspired Training</h3>
      <p>We provide six, two-hour food preparation sessions for our care-partners using local chefs, their recipes and locally grown food.</p>
      <span class="dot" style="background:radial-gradient(circle at 45% 40%,#8e4f8a,#6f8b3a 60%,#c0462e)" role="img" aria-label="Photo of fresh local vegetables"></span>
    </div>
    <div class="pledge" style="top:304px">
      <h3>Meaningful &amp; Engaging Activities</h3>
      <p>We provide a monthly list with local activities to our care-partners based on our client’s interest and capabilities. Focusing on what our client loved to do in the past.</p>
      <span class="dot" style="background:radial-gradient(circle at 50% 45%,#f1ece6,#cfc4b8 60%,#9a8f86)" role="img" aria-label="Photo of a senior man painting"></span>
    </div>
    <div class="pledge" style="top:402px">
      <h3>Home Solutions When Needed</h3>
      <p>We provide management services to help keep our clients in their homes by working with current contractors or locating new ones to properly maintain a safe-living environment.</p>
      <span class="dot" style="top:4px;background:radial-gradient(circle at 45% 35%,#f2c230,#b98a4e 55%,#6b5744)" role="img" aria-label="Photo of a contractor with a hard hat and tool belt"></span>
    </div>
  </div>

  <div class="panel about">
    <h2>About Owner</h2>
    <div class="photo" role="img" aria-label="Photo of a caregiver's hands gently holding an elderly hand"></div>
    <p class="about-text" style="top:217px">Dana Prewitt, owner of Brightwell Hearth Partners, has earned her certification as an Independent Trainer in the Kindred Pathway® Method (KPM) by Norla Vance, a nationally recognized instructor on natural aging and aging with Dementia. Dana is one of five certified independent trainers in the state of Lindhaven. All staff will have eight hours of hands on Dementia Kindred Pathway Method training.</p>
    <p class="about-sub">No two companies are alike!</p>
    <p class="about-text" style="top:370px">We provide our care-partners with the tools needed to handle the challenges of natural aging and living with Dementia / Alzheimer. Most seniors would rather be home instead of in a facility.</p>
    <p class="brand-name">Brightwell Hearth Partners</p>
    <span class="bubble" style="left:158px;top:478px;width:30px;height:30px;background:rgba(47,120,200,.25)"></span>
    <span class="bubble" style="left:184px;top:470px;width:18px;height:18px;background:rgba(47,120,200,.3)"></span>
  </div>

  <div class="inside-band">
    <svg viewBox="0 0 478 32" preserveAspectRatio="none"><polygon points="0,0 330,0 360,32 0,32" fill="#2b2a78"/><polygon points="340,22 478,22 478,32 348,32" fill="#2f8fc8"/><polygon points="330,0 478,0 478,8 337,8" fill="#1d78b4"/></svg>
    <span class="band-text" style="left:17px;bottom:9px;font-size:10px">brightwellhearthpartners.example</span>
    <span class="band-text" style="left:243px;bottom:9px;font-size:12px">410-555-0148</span>
  </div>
</section>

<section class="piece rack rack-back">
  <div class="band">
    <svg viewBox="0 0 244 30" preserveAspectRatio="none"><polygon points="0,0 178,0 198,30 0,30" fill="#2b2a78"/><polygon points="186,20 244,20 244,30 192,30" fill="#2f8fc8"/></svg>
    <span class="band-text" style="left:10px">brightwellhearthpartners.example</span>
  </div>
</section>
<section class="piece rack rack-front">
  <div class="photo hero" role="img" aria-label="Photo of a young caregiver hugging a smiling senior woman"></div>
  <div class="rack-top">
    <p class="brand-name">Brightwell<br>Hearth<br>Partners</p>
    <p class="welcome" style="top:148px">Welcome to<br>Brightwell Hearth Partners</p>
    <p class="phone-line" style="top:186px">410-555-0148</p>
    <p class="tagline" style="top:206px">Devoted to Thoughtful<br>Household Support.</p>
  </div>
  <div class="band">
    <svg viewBox="0 0 244 30" preserveAspectRatio="none"><polygon points="0,0 178,0 198,30 0,30" fill="#2b2a78"/><polygon points="186,20 244,20 244,30 192,30" fill="#2f8fc8"/></svg>
    <span class="band-text" style="left:10px">brightwellhearthpartners.example</span>
  </div>
</section>

<section class="piece insert insert-a">
  <div class="insert-head"><p class="brand-name">Brightwell Hearth Partners</p></div>
  <div class="stones-mark" role="img" aria-label="Shifting Stones program mark"></div>
  <p class="training">CAREGIVERS RECEIVE<strong>8 HOUR’S</strong>DEMENTIA TRAINING</p>
  <h2>Brain Change Model</h2>
  <p class="model-text">The STONES® model recognizes the dynamic nature of the human brain and its abilities. Unlike other cognitive models, it acknowledges that everyone’s abilities can change in a moment. Modifying environments, situations, interactions, and expectations will create either supportive positive opportunities or result in distress and a sense of failure. Just as gemstones need different settings and care to show their best characteristics, so do people. Rather than focusing on a person’s loss when there is brain change, seeing individuals as precious, unique, and capable encourages a care partnership and is the core of this model. Providing supportive settings for everyone, including care providers, allows them to use what they have to be their best. The STONES® advocate that everyone living with brain change when given the opportunity will shine.</p>
  <p class="model-credit">- Norla Vance and Kindred Pathway® Method Team</p>

  <div class="stone" style="top:433px;height:163px;--tone:var(--sapphire);--dot:#3f6fd0">
    <span class="stone-icon" style="background:radial-gradient(circle at 40% 35%,#b9b6f0,#4a3fa8 60%,#2a2170)" role="img" aria-label="Sapphire gemstone"></span>
    <h3>SAPPHIRE</h3>
    <p class="sub">True Blue<br>Optimal Cognition, Healthy Brain</p>
    <ul>
      <li>True to self: personal preferences remain basically the same</li>
      <li>Can be flexible in thinking and appreciate multiple perspectives</li>
      <li>Stress/pain/fatigue may trigger Diamond state: back to Sapphire with relief</li>
      <li>Able to suppress and filter personal reactions: chooses effective responses</li>
      <li>Selects from options and can make informed decisions</li>
      <li>Processes well and able to successfully transition</li>
      <li>Aging doesn’t change ability: processing slows, more effort/time/practice needed</li>
    </ul>
  </div>
  <div class="stone" style="top:596px;height:190px;--tone:var(--diamond);--dot:#8ab8de">
    <span class="stone-icon" style="background:radial-gradient(circle at 40% 35%,#ffffff,#cfd6de 55%,#8c959f)" role="img" aria-label="Diamond gemstone"></span>
    <h3>DIAMOND</h3>
    <p class="sub">Clear and Sharp<br>Routines and Rituals Rule</p>
    <ul>
      <li>Displays many facets: behavior and perspective can shift dramatically</li>
      <li>Prefers the familiar and may resist change: challenged by transitions</li>
      <li>More rigid and self-focused; sees wants as needs, when stressed</li>
      <li>Personal likes/dislikes in relationships/space/belongings etc, become more intense</li>
      <li>Reacts to changes in environment; benefits from familiar; functional/forgiving</li>
      <li>Needs repetition and time to absorb new/different information or routines</li>
      <li>Trusted authority figures can help: reacts better when respect is mutual</li>
    </ul>
  </div>
  <div class="insert-foot">410-555-0148 | brightwellhearthpartners.example</div>
</section>

<section class="piece insert insert-b">
  <div class="stone" style="top:0;height:196px;--tone:var(--emerald);--dot:#6fb52c">
    <span class="stone-icon" style="background:radial-gradient(circle at 40% 35%,#c9f0a0,#3a9a3a 55%,#145c2a)" role="img" aria-label="Emerald gemstone"></span>
    <h3>EMERALD</h3>
    <p class="sub">Green and On the Go With a Purpose<br>Naturally Flawed</p>
    <ul>
      <li>Sees self as able and independent, with limited awareness of changes in ability</li>
      <li>Lives in moments of clarity mixed with periods of loss in logic/reason/ perspective</li>
      <li>Understanding and use of language change: vague words and many repeats</li>
      <li>Cues and support help when getting to/from places and doing daily routines</li>
      <li>Awareness of time, place, and situation will not always match current reality</li>
      <li>Strong emotional reactions are triggered by fears, desires, or unmet needs</li>
    </ul>
  </div>
  <div class="stone" style="top:196px;height:222px;--tone:var(--amber);--dot:#ec8a1e">
    <span class="stone-icon" style="background:radial-gradient(circle at 40% 35%,#fff1a8,#f2b21e 55%,#b86a10)" role="img" aria-label="Amber gemstone"></span>
    <h3>AMBER</h3>
    <p class="sub">Caught in a Moment of Time<br>Caution Required</p>
    <ul>
      <li>Focused on sensation: seeks to satisfy desires and tries to avoid what is disliked</li>
      <li>Environment can drive actions and reactions without awareness of safety</li>
      <li>Visual abilities are limited: focus is on pieces or parts, not the whole picture</li>
      <li>What happens to or around an Amber, may cause strong and surprising reactions</li>
      <li>Enters others’ space and crosses boundaries attempting to meet own needs</li>
      <li>Has periods of intense activity: may be very curious or repetitive with objects or actions</li>
      <li>Care is refused or seen as threatening, due to differences in perspective and ability</li>
    </ul>
  </div>
  <div class="stone" style="top:418px;height:203px;--tone:var(--ruby);--dot:#d8281f">
    <span class="stone-icon" style="background:radial-gradient(circle at 40% 35%,#ff9a9a,#d81e2a 55%,#7a0a14)" role="img" aria-label="Ruby gemstone"></span>
    <h3>RUBY</h3>
    <p class="sub">Deep and Strong in Color<br>Others Stop Seeing What is Possible</p>
    <ul>
      <li>Makes use of rhythm: can usually sing, hum, pray, sway, rock, clap, and dance</li>
      <li>When moving can’t stop; when stopped can’t get moving: needs guidance and help</li>
      <li>Big, strong movements are possible, while skilled abilities are being lost</li>
      <li>Danger exists due to limited abilities combined with automatic actions or reactions</li>
      <li>Tends to miss subtle hints, but gets magnified facial expressions and voice rhythms</li>
      <li>Can mimic actions or motions, but will struggle to understand instruc-tions/gestures</li>
      <li>Able to pick up and hold objects, and yet not know what to do with them</li>
    </ul>
  </div>
  <div class="stone" style="top:621px;height:196px;--tone:var(--pearl);--dot:#c9a6d2">
    <span class="stone-icon" style="background:radial-gradient(circle at 40% 35%,#fff7ea,#e2c6a4 55%,#a88660)" role="img" aria-label="Pearl"></span>
    <h3>PEARL</h3>
    <p class="sub">Hidden Within a Shell<br>Beautiful Moments to Behold</p>
    <ul>
      <li>Will frequently recognize familiar touches, voices, faces, aromas, and tastes</li>
      <li>Personhood survives, although all other capabilities are minimal</li>
      <li>Understanding input takes time: go slow and simplify for success</li>
      <li>In care, first get connected by offering comfort then use careful and caring touch</li>
      <li>Changes in the body are profound: weight loss, immobility, systems are failing</li>
      <li>As protective reflexes are lost, breathing, swallowing, and moving will be difficult</li>
      <li>Care partners benefit from learning the art of letting go rather than simply giving up</li>
    </ul>
  </div>
  <div class="base"></div>
</section>

</body>
</html>
```